LEARN Business Skills so you can Earn a good living

size of the poster is 8”x 10.75" plus 0.25" bleed.
Please leave 1 inch on the bottoum for footer
I want a design a poster that will attract people's attention.
I appreciate a creative ad however the ad should not take away from being able to clearly read the text.
-I also appreciate a simple creative ad that is not too busy.
-you can use graphics, vectors, or pictures of real people.
-however, if you use real people it should be a white male that is wearing a white shirt and look like a professional person.

Target Market(s)

Potential young business people

Industry/Entity Type

education

Requirements
Must have
• easy to read the text
Nice to have
• I would like a "creative" simple ad that is easy to be read
Should not have
• pictures of women

```html
<!DOCTYPE html>
<html lang="en">
<head>
<meta charset="utf-8">
<title>Learn It To Earn It – Business Enrichment Course</title>
<link href="https://fonts.googleapis.com/css2?family=Poppins:wght@300;500;600;700;800&display=swap" rel="stylesheet">
<style>
  :root {
    --ink: #1c1c1c;
    --paper: #ffffff;
    --band: #262626;
    --photo-light: #f4f4f4;
    --photo-mid: #d9d9d9;
    --photo-dark: #5a5a5a;
    --rule: #cfcfcf;
    --icon-bg: #6b6b6b;
    --line-light: #bdbdbd;
  }
  * { margin: 0; padding: 0; box-sizing: border-box; }
  html, body { width: 800px; height: 1200px; overflow: hidden; background: var(--paper); }
  body { font-family: 'Poppins', sans-serif; color: var(--ink); }
  .poster { position: relative; width: 800px; height: 1200px; overflow: hidden; background: var(--paper); }

  .office-backdrop {
    position: absolute; left: 0; top: 150px; width: 800px; height: 662px;
    background: linear-gradient(180deg, var(--paper) 0%, var(--photo-light) 35%, var(--photo-mid) 100%);
  }
  .headline { position: absolute; left: 40px; top: 30px; line-height: 1; white-space: nowrap; z-index: 2; }
  .headline .row { display: block; }
  .headline .heavy { font-weight: 800; }
  .headline .light { font-weight: 300; }
  .headline .row-learn { font-size: 176px; letter-spacing: -6px; }
  .headline .row-earn { font-size: 118px; letter-spacing: -4px; margin-top: -14px; }

  .presenter-photo {
    position: absolute; left: 506px; top: 283px; width: 294px; height: 529px; z-index: 3;
    background: linear-gradient(180deg, #8c8c8c 0%, var(--photo-dark) 45%, #3d3d3d 100%);
    border-radius: 120px 120px 0 0;
  }
  .laptop-shape {
    position: absolute; left: 318px; top: 705px; width: 270px; height: 107px; z-index: 2;
    background: linear-gradient(160deg, #e6ece9, #c9d2ce);
    clip-path: polygon(0 20%, 72% 0, 100% 100%, 18% 100%);
  }

  .rule { position: absolute; left: 45px; width: 490px; height: 1px; background: var(--rule); z-index: 2; }
  .rule-top { top: 358px; }
  .rule-bottom { top: 605px; }

  .course-title {
    position: absolute; left: 42px; top: 370px; z-index: 2;
    font-weight: 800; font-size: 62px; line-height: 68px; letter-spacing: -1px; text-transform: uppercase;
  }
  .tagline {
    position: absolute; left: 45px; top: 628px; z-index: 2;
    font-weight: 700; font-size: 30px; line-height: 41px; letter-spacing: -0.5px;
  }

  .skills-band { position: absolute; left: 0; top: 812px; width: 800px; height: 388px; background: var(--band); color: var(--paper); }
  .skills-frame { position: absolute; left: 54px; top: 68px; }
  .skills-pill {
    position: absolute; left: 96px; top: 40px; width: 606px; height: 50px; border-radius: 25px;
    background: var(--paper); color: var(--ink); text-align: center;
    font-weight: 700; font-size: 29px; line-height: 50px; letter-spacing: -0.3px;
  }
  .benefit { position: absolute; top: 110px; width: 220px; text-align: center; }
  .benefit-icon { display: block; margin: 0 auto 6px; }
  .benefit-label { font-weight: 600; font-size: 19px; line-height: 24px; }
  .benefit-job { left: 70px; }
  .benefit-business { left: 290px; top: 114px; }
  .benefit-salary { left: 523px; }
  .divider { position: absolute; top: 94px; width: 1px; height: 115px; background: #555; }
  .divider-a { left: 282px; }
  .divider-b { left: 517px; }

  .subject-list {
    position: absolute; left: 20px; top: 274px; width: 760px; text-align: center;
    font-weight: 500; font-size: 12.5px; line-height: 16px; text-transform: uppercase; color: #f0f0f0;
  }
</style>
</head>
<body>
<div class="poster">
  <div class="office-backdrop" role="img" aria-label="Softly blurred bright office interior in grey tones"></div>

  <h1 class="headline">
    <span class="row row-learn"><span class="heavy">LEARN</span> <span class="light">IT</span></span>
    <span class="row row-earn"><span class="light">TO</span> <span class="heavy">EARN</span> <span class="light">IT</span></span>
  </h1>

  <div class="presenter-photo" role="img" aria-label="Young professional man in a grey suit, white shirt and tie, leaning over a laptop"></div>
  <div class="laptop-shape" role="img" aria-label="Open laptop lid"></div>

  <div class="rule rule-top"></div>
  <h2 class="course-title">Business<br>Enrichment<br>Course</h2>
  <div class="rule rule-bottom"></div>
  <p class="tagline">A proven success of<br>helping people in<br>their livelihoods</p>

  <section class="skills-band">
    <svg class="skills-frame" width="692" height="180" viewBox="0 0 692 180">
      <rect x="0.75" y="0.75" width="690.5" height="178.5" rx="18" fill="none" stroke="var(--line-light)" stroke-width="1.5"/>
    </svg>
    <div class="skills-pill">BUSINESS SKILLS THAT WILL HELP YOU</div>

    <div class="benefit benefit-job">
      <svg class="benefit-icon" width="58" height="58" viewBox="0 0 58 58">
        <circle cx="29" cy="29" r="27" fill="var(--icon-bg)" stroke="#9a9a9a" stroke-width="2"/>
        <rect x="18" y="15" width="22" height="20" rx="3" fill="none" stroke="#fff" stroke-width="1.8"/>
        <circle cx="29" cy="31" r="6" fill="none" stroke="#fff" stroke-width="1.8"/>
        <path d="M25 36 L23 44 L29 41 L35 44 L33 36" fill="none" stroke="#fff" stroke-width="1.8" stroke-linejoin="round"/>
        <path d="M22 21 h14" stroke="#fff" stroke-width="1.8"/>
      </svg>
      <div class="benefit-label">Get a<br>quality job</div>
    </div>
    <div class="divider divider-a"></div>

    <div class="benefit benefit-business">
      <svg class="benefit-icon" width="58" height="58" viewBox="0 0 58 58">
        <circle cx="29" cy="29" r="27" fill="var(--icon-bg)" stroke="#9a9a9a" stroke-width="2"/>
        <rect x="16" y="33" width="5" height="8" fill="none" stroke="#fff" stroke-width="1.6"/>
        <rect x="24" y="29" width="5" height="12" fill="none" stroke="#fff" stroke-width="1.6"/>
        <rect x="32" y="25" width="5" height="16" fill="none" stroke="#fff" stroke-width="1.6"/>
        <path d="M16 27 L25 21 L31 23 L41 15 M36 15 h5 v5" fill="none" stroke="#fff" stroke-width="1.8" stroke-linejoin="round"/>
      </svg>
      <div class="benefit-label">Start/grow<br>your business</div>
    </div>
    <div class="divider divider-b"></div>

    <div class="benefit benefit-salary">
      <svg class="benefit-icon" width="58" height="58" viewBox="0 0 58 58">
        <circle cx="29" cy="29" r="27" fill="var(--icon-bg)" stroke="#9a9a9a" stroke-width="2"/>
        <rect x="16" y="27" width="26" height="13" rx="2" fill="none" stroke="#fff" stroke-width="1.8"/>
        <circle cx="29" cy="33.5" r="3" fill="none" stroke="#fff" stroke-width="1.6"/>
        <path d="M16 43 h26" stroke="#fff" stroke-width="1.6"/>
        <path d="M18 22 L25 17 L30 20 L39 13 M35 13 h4 v4" fill="none" stroke="#fff" stroke-width="1.8" stroke-linejoin="round"/>
      </svg>
      <div class="benefit-label">Increase your<br>salary</div>
    </div>

    <p class="subject-list">
      Business Admiistration &nbsp;|&nbsp; Small Business Management &nbsp;|&nbsp; Finance | Investments &nbsp;|&nbsp; Computers &nbsp;|&nbsp; Accounting<br>
      Sales &nbsp;|&nbsp; Marketing &nbsp;|&nbsp; Project Management Interviewing Skills &nbsp;|&nbsp; Business Law &nbsp;|&nbsp; Negotiation &nbsp;|&nbsp; Public Speaking<br>
      Import/Export &nbsp;|&nbsp; Information Technoloy &nbsp;|&nbsp; Distribution &nbsp;|&nbsp; Marketing &nbsp;|&nbsp; Ledgerly &nbsp;|&nbsp; Real Estate<br>
      Health Care-Management &nbsp;|&nbsp; MarketRiver
    </p>
  </section>
</div>
</body>
</html>
```